Bookcover: Ways to Turn Into a Bold Pathfinder

I am publishing a super-low-cost innovation book for €4,99 on Quillmere Open Press to help everyone become a great innovator: young ambitious people without college education nor a big budget. Do you want to help me?

Brief:
Design a book cover 1600 x 2560 pixels for QOP.
Main title: Ways to Turn Into a Bold Pathfinder
Sub title: mindset - insights - skills & tools
Author: Joost ter Brakel
Design: captive, and appealing to everyone
Target Group: young ambitious people without college education

For quillmere please format the height/width ratio of 1.6:1

```html
<!DOCTYPE html>
<html lang="en">
<head>
<meta charset="utf-8">
<title>Ways to Turn Into a Bold Pathfinder — Book Cover</title>
<link href="https://fonts.googleapis.com/css2?family=Bebas+Neue&family=Roboto:wght@400;500&display=swap" rel="stylesheet">
<style>
  :root {
    --backdrop: #9f9e9f;
    --paper: #ffffff;
    --ink: #231f20;
    --signal-red: #c00000;
    --bulb-yellow: #f2cb33;
    --bulb-metal: #9a9a9a;
  }
  html, body {
    margin: 0;
    padding: 0;
    width: 1200px;
    height: 1200px;
    overflow: hidden;
    background: var(--backdrop);
  }
  .cover {
    position: absolute;
    left: 293px;
    top: 140px;
    width: 614px;
    height: 920px;
    background: var(--paper);
    overflow: hidden;
  }
  .book-title { margin: 0; }
  .title-line {
    position: absolute;
    left: 33px;
    font-family: "Bebas Neue", "Oswald", sans-serif;
    font-weight: 400;
    line-height: 1;
    color: var(--ink);
    white-space: nowrap;
  }
  .title-line--one { top: 17px; font-size: 157px; }
  .title-line--two { top: 132px; font-size: 157px; }
  .title-line--three { top: 249px; font-size: 208px; }

  .idea-mark {
    position: absolute;
    left: 480px;
    top: 280px;
    width: 126px;
    height: 142px;
  }
  .idea-mark__ball {
    position: absolute;
    left: 27px;
    top: 26px;
    width: 72px;
    height: 72px;
    border-radius: 50%;
    background: radial-gradient(circle at 40% 35%, #f8dc5c, var(--bulb-yellow) 60%, #d9ad1c);
  }
  .idea-mark__base {
    position: absolute;
    left: 45px;
    top: 104px;
    width: 36px;
    height: 36px;
    border-radius: 4px 4px 50% 50%;
    background: linear-gradient(180deg, #c9c9c9, var(--bulb-metal) 60%, #6c6c6c);
  }
  .idea-mark__rays {
    position: absolute;
    left: 0;
    top: 0;
  }

  .highlight-band {
    position: absolute;
    left: 0;
    top: 441px;
    width: 614px;
    height: 167px;
  }
  .highlight-word {
    position: absolute;
    left: 0;
    right: 0;
    top: 462px;
    margin: 0;
    text-align: center;
    font-family: "Bebas Neue", "Oswald", sans-serif;
    font-weight: 400;
    font-size: 156px;
    line-height: 1;
    color: var(--paper);
    white-space: nowrap;
  }

  .subtitle {
    position: absolute;
    left: 33px;
    top: 657px;
    margin: 0;
    width: 570px;
    font-family: "Roboto", "Helvetica Neue", sans-serif;
    font-weight: 500;
    font-size: 50px;
    line-height: 56px;
    color: var(--ink);
    letter-spacing: -0.5px;
  }

  .author {
    position: absolute;
    left: 33px;
    top: 809px;
    margin: 0;
    font-family: "Bebas Neue", "Oswald", sans-serif;
    font-weight: 400;
    font-size: 72px;
    line-height: 1;
    color: var(--ink);
    white-space: nowrap;
  }
  .author__surname { color: var(--signal-red); }
</style>
</head>
<body>
  <main class="cover">
    <h1 class="book-title">
      <span class="title-line title-line--one">Ways to</span>
      <span class="title-line title-line--two">Turn into</span>
      <span class="title-line title-line--three">A Bold</span>
    </h1>

    <div class="idea-mark">
      <svg class="idea-mark__rays" width="126" height="142" viewBox="0 0 126 142" aria-hidden="true">
        <g stroke="#231f20" stroke-width="2" stroke-linecap="round" fill="none">
          <line x1="63" y1="2" x2="62" y2="17"/>
          <line x1="19" y1="22" x2="30" y2="32"/>
          <line x1="106" y1="22" x2="95" y2="33"/>
          <line x1="1" y1="62" x2="16" y2="62"/>
          <line x1="108" y1="62" x2="124" y2="62"/>
          <line x1="18" y1="108" x2="30" y2="98"/>
          <line x1="97" y1="93" x2="108" y2="102"/>
        </g>
      </svg>
      <div class="idea-mark__ball" role="img" aria-label="Crumpled yellow paper ball forming a light bulb"></div>
      <div class="idea-mark__base" role="img" aria-label="Metal screw base of the light bulb"></div>
    </div>

    <svg class="highlight-band" width="614" height="167" viewBox="0 0 614 167" aria-hidden="true">
      <path fill="#c00000" stroke="#ffffff" stroke-width="2" stroke-linejoin="round"
        d="M0 7 L30 5 L55 7 L90 4 L130 6 L160 3 L200 6 L240 5 L270 7 L300 4 L340 6 L380 3 L410 6 L450 4 L490 7 L520 4 L560 6 L590 3 L614 5
           L614 161 L585 163 L550 160 L520 164 L480 161 L450 163 L410 160 L370 163 L340 161 L300 164 L260 161 L230 163 L190 160 L150 163 L120 161 L80 164 L55 160 L30 162 L0 160 Z"/>
    </svg>
    <p class="highlight-word">Pathfinder</p>

    <p class="subtitle">MINDSET - INSIGHTS -<br>SKILLS &amp; TOOLS</p>

    <p class="author">Joost ter <span class="author__surname">Brakel</span></p>
  </main>
</body>
</html>
```